Flat bootstrap design for existing site

I'm looking for a modern flat design based around an existing logo. This has to be a custom design (no external templates), and implemented into a bootstrap framework.

The logo is attached as 2 versions - choose whichever you want, that flows better with whatever design you choose.

Added screenshots of the existing site (currently using the default bootstrap layouts). Please make your designs around those pages in the screenshots (i.e. the homepage only has the postal code input and the header). The active page has 3 screenshots, because I wanted to illustrate the other states that would be visible (in the table rows).

This is a moving/junk removal website, just for some context.

Here's some example websites (flat designs) that I like, just to give you an idea of what I'm after.

https://www.plimvora.com/
https://dacklow.com/
https://trevanu.com/
https://quobrintal.com/en/

Coding

Coded - Design and coding required

Number of Pages Required

5+ page

Colors

Designer to choose colors to be used in the design.

Requirements
Must have
• It must be a modern/simple flat design, that is built around the existing logo (attached).
• It has to be implemented using bootstrap.

```html
<!DOCTYPE html>
<html lang="en">
<head>
<meta charset="utf-8">
<title>Haulbrio – Book Junk Removal</title>
<link rel="stylesheet" href="https://fonts.googleapis.com/css2?family=Nunito:wght@400;600;800&display=swap">
<style>
  :root {
    --sky: #45c6f3;
    --sky-light: #5ccff6;
    --sky-deep: #2bbdf0;
    --white: #ffffff;
    --heading-blue: #2e86c8;
    --button-blue: #4cc6f0;
    --input-border: #cfd6db;
    --text-dark: #2a2a2a;
  }
  * { box-sizing: border-box; margin: 0; padding: 0; }
  html, body {
    width: 1200px;
    height: 624px;
    overflow: hidden;
    font-family: "Nunito", Arial, sans-serif;
  }
  .page {
    position: relative;
    width: 1200px;
    height: 624px;
    overflow: hidden;
    background: var(--sky);
  }
  .page-backdrop {
    position: absolute;
    inset: 0;
    background:
      linear-gradient(135deg, var(--sky-light) 0%, var(--sky) 40%, var(--sky-deep) 70%, var(--sky-light) 100%);
  }
  .site-header {
    position: absolute;
    top: 0;
    left: 0;
    width: 1200px;
    height: 100px;
  }
  .brand {
    position: absolute;
    left: 86px;
    top: 26px;
    display: flex;
    align-items: center;
    gap: 10px;
    color: var(--white);
    font-weight: 800;
    font-size: 38px;
    letter-spacing: 1px;
    line-height: 1;
  }
  .brand-dot {
    width: 16px;
    height: 16px;
    border-radius: 50%;
    background: var(--white);
  }
  .main-nav {
    position: absolute;
    top: 39px;
    right: 89px;
    display: flex;
    gap: 52px;
  }
  .main-nav a {
    color: var(--white);
    text-decoration: none;
    font-size: 16px;
    font-weight: 400;
    letter-spacing: 0.2px;
  }
  .booking-card {
    position: absolute;
    left: 272px;
    top: 212px;
    width: 657px;
    height: 220px;
    background: var(--white);
    border-radius: 6px;
    box-shadow: 0 6px 24px rgba(20, 90, 130, 0.18);
    text-align: center;
  }
  .booking-title {
    margin-top: 56px;
    color: var(--heading-blue);
    font-size: 30px;
    font-weight: 400;
    letter-spacing: 0.3px;
    line-height: 1.2;
  }
  .booking-form {
    position: absolute;
    left: 123px;
    top: 122px;
    width: 409px;
    height: 44px;
    display: flex;
    border: 1px solid var(--input-border);
    border-radius: 22px;
    overflow: hidden;
    box-shadow: 0 2px 5px rgba(0, 0, 0, 0.12);
  }
  .postal-input {
    flex: 1;
    border: none;
    outline: none;
    padding-left: 20px;
    font-family: "Nunito", Arial, sans-serif;
    font-size: 13px;
    color: var(--text-dark);
    background: var(--white);
  }
  .postal-input::placeholder { color: var(--text-dark); opacity: 1; }
  .book-button {
    width: 86px;
    border: none;
    background: var(--button-blue);
    color: var(--white);
    font-family: "Nunito", Arial, sans-serif;
    font-size: 16px;
    letter-spacing: 0.3px;
  }
</style>
</head>
<body>
  <div class="page">
    <div class="page-backdrop" role="img" aria-label="Low-poly pattern of light blue triangles"></div>

    <header class="site-header">
      <div class="brand"><span class="brand-dot"></span>Haulbrio</div>
      <nav class="main-nav">
        <a href="#">BOOK</a>
        <a href="#">HOW IT WORKS</a>
        <a href="#">BECOME A DRIVER</a>
        <a href="#">SIGN IN</a>
      </nav>
    </header>

    <section class="booking-card">
      <h1 class="booking-title">NEED JUNK REMOVED? BOOK NOW</h1>
      <form class="booking-form">
        <input class="postal-input" type="text" placeholder="Postal code">
        <button class="book-button" type="button">BOOK</button>
      </form>
    </section>
  </div>
</body>
</html>
```